quickdeedsale.com redesign with wireframes, white space and custom form are very important

Need a new two column design that will convert easily to mobile responsive. Lots of white space. Winning design will probably be based on header area and making the custom form stand out. I want the header to be very much like www.tallgatevk.com except the form not to go up into the header.
Here are some of the websites I really like:
www.birchdwell.com
http://ourplotpurchasedirect.com/
http://kellbrightproperty.com/

We buy homes for cash and close fast. Our target is a home seller who is desperate to sell quickly.
I have uploaded my really ugly wireframe and my logo. I also uploaded my photo for the about us box and a possible photo to use for the header.
The copy on the wireframe is what I will be using except for the about us box.

Here is the exact link for video to frame in the top left box.
https://clipvault.example/Qm38pzrtLa

0592cd
85cae6
eaf1f7
fbee3d
ec1f27

• Everything on wireframe.
• Must use Verdana font and nothing should be smaller than 12 point. Most should be in 14 point. (except maybe inside of form)

```html
<!DOCTYPE html>
<html lang="en">
<head>
<meta charset="utf-8">
<title>quickdeedsale.com – Sell Your Home Fast</title>
<link rel="stylesheet" href="https://fonts.googleapis.com/css2?family=Noto+Sans:wght@400;700&display=swap">
<style>
:root{
  --blue:#0592cd;
  --blue-dark:#04709e;
  --sky:#85cae6;
  --mist:#eaf1f7;
  --yellow:#fbee3d;
  --gold:#f5b400;
  --red:#ec1f27;
  --ink:#1d1d1d;
  --text:#333333;
  --muted:#666666;
  --panel:#232323;
  --field:#ffffff;
  --green:#3a9b2c;
  --grey-bg:#e4e4e4;
  --box-bg:#efefef;
  --footer:#ebebeb;
  --rule:#cfcfcf;
}
*{box-sizing:border-box;margin:0;padding:0}
html,body{width:1200px;height:3109px;overflow:hidden}
body{font-family:Verdana,"Noto Sans",sans-serif;color:var(--text);background:#fff;font-size:16px;line-height:1.45}
.page{position:relative;width:1200px;height:3109px;overflow:hidden}
.abs{position:absolute}

/* header */
.site-header{left:0;top:0;width:1200px;height:135px;background:#fff}
.brand{left:110px;top:40px;display:flex;align-items:center;gap:12px}
.brand-mark{width:34px;height:34px;background:var(--red)}
.brand-name{font-size:30px;font-weight:700;color:var(--ink);letter-spacing:-.5px}
.social-top{left:974px;top:25px;display:flex;gap:4px}
.social-top span{width:26px;height:26px;display:block}
.hotline{left:855px;top:62px;display:flex;align-items:center;gap:10px}
.hotline-text{font-size:17px;line-height:1.15;color:var(--ink)}
.hotline-text strong{display:block;color:var(--red);font-size:28px;font-weight:400}

.main-nav{left:0;top:135px;width:1200px;height:47px;background:var(--blue)}
.main-nav ul{list-style:none;display:flex;margin-left:110px;height:47px}
.main-nav li{color:#fff;font-size:14px;text-transform:uppercase;display:flex;align-items:center;justify-content:center;border-right:1px solid rgba(255,255,255,.25)}
.main-nav li.active{background:var(--blue-dark)}

.hero{left:0;top:182px;width:1200px;height:330px;background:linear-gradient(180deg,#6fa6d6 0%,#9cc4e6 30%,#cbb79a 62%,#8f8774 100%)}
.hero-caption{left:0;top:446px;width:1200px;height:66px;background:rgba(20,20,20,.72);color:#fff;font-size:26px;padding:15px 0 0 110px}
.hero-caption b{color:var(--yellow)}

/* intro */
.intro{left:110px;top:560px;width:500px}
.section-title{font-size:23px;line-height:1.3;color:var(--ink);text-transform:uppercase;font-weight:400}
.ticks{list-style:none;margin:18px 0 0 18px}
.ticks li{display:flex;align-items:center;gap:10px;font-size:16px;margin-bottom:9px}
.ticks svg{flex:none}
.intro-note{font-size:16px;margin-top:16px;color:var(--ink)}
.video{left:110px;top:837px;width:491px;height:301px;background:linear-gradient(135deg,#3a3f45,#1b1d20)}
.video svg{position:absolute;left:213px;top:118px}

.lead-form{left:682px;top:553px;width:410px;height:593px;background:var(--panel)}
.form-head{height:94px;background:linear-gradient(180deg,var(--yellow),var(--gold));color:var(--ink);font-size:25px;font-weight:700;text-align:center;line-height:1.25;padding-top:14px}
.form-head::after{content:"";position:absolute;left:185px;top:94px;border:20px solid transparent;border-top:14px solid var(--gold);border-bottom:0}
.form-body{padding:24px 18px 0}
.form-intro{color:#fff;font-size:14px;margin-bottom:12px}
.field{background:var(--field);height:38px;margin-bottom:10px;font-size:12px;color:#999;padding:10px 8px}
.field-row{display:flex;gap:18px}
.field-row .field{flex:1}
.field.tall{height:120px}
.submit{display:block;margin:22px auto 0;width:320px;height:52px;background:var(--red);color:#fff;font-size:20px;text-align:center;line-height:52px;border-radius:4px}

/* content band */
.band{left:0;top:1198px;width:1200px;height:1550px;background:var(--grey-bg);border-top:2px solid var(--rule)}
.content-box{left:110px;top:1233px;width:533px;height:1540px;background:#fff;border:1px solid var(--rule)}
.content-inner{left:122px;top:1246px;width:510px}
.blue-title{font-size:23px;line-height:1.3;color:var(--blue);text-transform:uppercase;font-weight:400}
.copy{font-size:15px;line-height:1.6;margin-top:6px}
.copy .hl{color:var(--red)}
.sub-title{font-size:23px;line-height:1.3;color:var(--ink);text-transform:uppercase;font-weight:400;margin-top:22px}
.ticks.small{margin:14px 0 0 22px}
.ticks.small li{font-size:15px;margin-bottom:6px}
.ticks.small li.hl{color:var(--red)}
.help{font-size:23px;color:var(--blue);line-height:1.35;margin-top:22px}

.ribbon{height:46px;color:#fff;font-size:20px;padding:9px 0 0 20px}
.ribbon.red{background:var(--red)}
.ribbon.blue{background:var(--blue)}
.blog-ribbon{left:97px;top:1809px;width:546px}
.archive-ribbon{left:97px;top:2586px;width:546px}

.post{left:124px;width:505px;height:200px}
.post-meta{font-size:12px;color:var(--muted);display:flex;gap:12px}
.post-meta em{font-style:normal;color:var(--blue)}
.post-thumb{position:absolute;left:0;top:30px;width:193px;height:134px;background:linear-gradient(180deg,#8cc0e2 0%,#b77a5a 45%,#6d9a4d 100%)}
.post-text{position:absolute;left:201px;top:30px;width:304px;font-size:13.5px;line-height:1.55;color:var(--ink)}
.post-actions{position:absolute;left:201px;top:130px;display:flex;font-size:13px;color:#fff}
.post-actions span{height:36px;line-height:36px;padding:0 12px}
.post-actions .count{background:var(--red);width:120px}
.post-actions .reply{background:var(--panel);width:184px}

.pager{left:124px;top:2522px;display:flex;gap:10px}
.pager span{width:30px;height:30px;background:var(--panel);color:#fff;font-size:14px;text-align:center;line-height:30px}
.pager span.on{background:var(--red)}
.tags{left:126px;top:2653px;width:500px;display:flex;flex-wrap:wrap;gap:10px}
.tags span{background:var(--panel);color:#fff;font-size:15px;height:44px;line-height:44px;padding:0 20px}

/* sidebar */
.privacy-tab{left:682px;top:1231px;width:190px;height:46px;background:var(--blue);color:#fff;font-size:16px;text-align:center;line-height:46px}
.side-social{left:950px;top:1245px;display:flex;gap:12px}
.side-social span{width:16px;height:16px;background:#aaa;border-radius:50%}
.call-bar{left:682px;top:1289px;width:410px;height:69px;background:var(--panel);color:#fff;font-size:17px;line-height:1.35;padding:10px 12px}
.side-box{left:682px;width:410px;background:var(--box-bg);border:1px solid var(--rule);padding:12px}
.side-box .inner{background:var(--box-bg);border:1px solid #dadada;padding:14px 12px;height:100%}
.side-title{font-size:22px;color:var(--ink);font-weight:400;line-height:1.3}
.side-copy{font-size:14px;line-height:1.55;margin-top:10px;color:var(--ink)}
.quote-by{text-align:right;font-size:15px;margin-top:12px;color:var(--ink)}
.quote-by b{color:var(--red);font-weight:400}
.about-photo{position:absolute;right:26px;top:20px;width:104px;height:152px;background:linear-gradient(180deg,#9cc1dc,#607a8e)}
.cities{display:grid;grid-template-columns:1fr 1fr;column-gap:20px;margin-top:12px}
.cities span{font-size:14px;color:var(--ink);display:flex;align-items:center;gap:8px;line-height:23.5px}
.cities span::before{content:"";width:12px;height:12px;border:1px solid #999;background:#fff}
.view-all{text-align:right;font-size:13px;text-decoration:underline;color:var(--ink);margin-top:6px}
.note-red{color:var(--red);font-size:14px;margin-top:10px;line-height:1.5}
.buy-pics{display:flex;gap:14px;margin-top:14px}
.buy-pics div{width:176px;height:104px;background:linear-gradient(180deg,#8cc0e2 0%,#c9a98a 50%,#6c9a4c 100%)}

/* footer */
.site-footer{left:0;top:2808px;width:1200px;height:249px;background:var(--footer);border-top:1px solid var(--rule)}
.foot-col{top:2820px}
.foot-title{font-size:17px;font-weight:700;color:var(--ink);letter-spacing:.5px;padding-bottom:12px;border-bottom:1px solid var(--rule);margin-bottom:20px;width:170px}
.foot-text{font-size:15px;line-height:1.4;color:var(--text)}
.foot-list{list-style:none;font-size:15px;line-height:1.4}
.foot-list li{display:flex;align-items:center;gap:14px}
.foot-list .dot{width:10px;height:10px;background:#999;border-radius:50%}
.contact-line{display:flex;gap:14px;font-size:15px;line-height:1.4;margin-bottom:12px}
.contact-line a{color:var(--blue)}
.legal{left:0;top:3057px;width:1200px;height:52px;background:#fff;font-size:14px;color:var(--ink)}
.legal .left{position:absolute;left:110px;top:16px}
.legal .right{position:absolute;right:110px;top:16px}
</style>
</head>
<body>
<div class="page">

  <header class="site-header abs">
  </header>
  <div class="brand abs"><span class="brand-mark"></span><span class="brand-name">quickdeedsale.com</span></div>
  <div class="social-top abs" aria-label="Social links">
    <span style="background:#3b5a98"></span><span style="background:#29a9e1"></span><span style="background:#d8432e"></span><span style="background:#0e76a8"></span>
  </div>
  <div class="hotline abs">
    <svg width="36" height="36" viewBox="0 0 24 24" aria-hidden="true"><path fill="#333" d="M6.6 10.8a15 15 0 0 0 6.6 6.6l2.2-2.2c.3-.3.7-.4 1-.2 1.1.4 2.3.6 3.6.6.6 0 1 .4 1 1V20c0 .6-.4 1-1 1A17 17 0 0 1 3 4c0-.6.4-1 1-1h3.5c.6 0 1 .4 1 1 0 1.3.2 2.5.6 3.6.1.3 0 .7-.2 1z"/></svg>
    <div class="hotline-text">Nights and weekends ok<strong>407-555-0142</strong></div>
  </div>

  <nav class="main-nav abs">
    <ul>
      <li class="active" style="width:95px">Home</li>
      <li style="width:200px">Sell Your Home</li>
      <li style="width:150px">How It Works</li>
      <li style="width:222px">Stop Foreclosure</li>
      <li style="width:136px">Probate</li>
      <li style="width:170px;border-right:0">Contact Us</li>
    </ul>
  </nav>

  <div class="hero abs" role="img" aria-label="Photo of a two-storey suburban house with a tall pine tree under a blue sky"></div>
  <div class="hero-caption abs">Sell Your Home for <b>Cash</b> in 8 Days We Buy <b>Houses Nationwide.</b></div>

  <section class="intro abs">
    <h1 class="section-title">These are the benefits of selling your home to us:</h1>
    <ul class="ticks">
      <li><svg width="16" height="14" viewBox="0 0 16 14"><path d="M1 7l5 5L15 1" stroke="var(--green)" stroke-width="2.5" fill="none"/></svg>You pick the closing date.</li>
      <li><svg width="16" height="14" viewBox="0 0 16 14"><path d="M1 7l5 5L15 1" stroke="var(--green)" stroke-width="2.5" fill="none"/></svg>You pay NO Commissions or Fees.</li>
      <li><svg width="16" height="14" viewBox="0 0 16 14"><path d="M1 7l5 5L15 1" stroke="var(--green)" stroke-width="2.5" fill="none"/></svg>You don't have to paint, clean or make repairs</li>
    </ul>
    <p class="intro-note">Watch to see our president Grant explain how easy it is to sell to us:</p>
  </section>
  <div class="video abs" role="img" aria-label="Video player for https://clipvault.example/Qm38pzrtLa showing the company president">
    <svg width="64" height="64" viewBox="0 0 64 64" aria-hidden="true"><path d="M14 6l44 26-44 26z" fill="#fff"/></svg>
  </div>

  <form class="lead-form abs">
    <div class="form-head">Yes, I Want to Sell My<br>Home Fast!</div>
    <div class="form-body">
      <p class="form-intro">Get a no obligation written offer in 36 hours</p>
      <div class="field">Your Name:</div>
      <div class="field">Your Phone Number:</div>
      <div class="field">Your Email Address:</div>
      <div class="field">Property address including City, State &amp; Zip code:</div>
      <div class="field-row"><div class="field">Repairs needed if any:</div><div class="field">Asking Price:</div></div>
      <div class="field tall">Comments</div>
      <span class="submit">SUBMIT, TO GET STARTED</span>
    </div>
  </form>

  <div class="band abs"></div>
  <div class="content-box abs"></div>
  <section class="content-inner abs">
    <h2 class="blue-title">These are the benefits of selling your home to us:</h2>
    <p class="copy">Selling a home on your own has never been easier. From Orlando to Greensboro - and all points in between- you can sell your home today without any hassles. Call <span class="hl">1-800-555-0199</span> or fill out the form below to get a written offer on your home in just 36 hours. Sell today online to people that care.</p>
    <h2 class="sub-title">If you need to sell a home fast because of:</h2>
    <ul class="ticks small">
      <li><svg width="16" height="14" viewBox="0 0 16 14"><path d="M1 7l5 5L15 1" stroke="var(--green)" stroke-width="2.5" fill="none"/></svg>Divorce or Bankruptcy</li>
      <li><svg width="16" height="14" viewBox="0 0 16 14"><path d="M1 7l5 5L15 1" stroke="var(--green)" stroke-width="2.5" fill="none"/></svg>Foreclosure</li>
      <li class="hl"><svg width="16" height="14" viewBox="0 0 16 14"><path d="M1 7l5 5L15 1" stroke="var(--green)" stroke-width="2.5" fill="none"/></svg>Landlord problems - evictions with tenants okay</li>
      <li><svg width="16" height="14" viewBox="0 0 16 14"><path d="M1 7l5 5L15 1" stroke="var(--green)" stroke-width="2.5" fill="none"/></svg>Inherited property in probate</li>
      <li><svg width="16" height="14" viewBox="0 0 16 14"><path d="M1 7l5 5L15 1" stroke="var(--green)" stroke-width="2.5" fill="none"/></svg>Termites, mold, flood or fire damage, leaky roof</li>
      <li><svg width="16" height="14" viewBox="0 0 16 14"><path d="M1 7l5 5L15 1" stroke="var(--green)" stroke-width="2.5" fill="none"/></svg>Moving or can't afford mortgage payments</li>
    </ul>
    <p class="help">We Can Help.<br>We are the fastest home buyers around.</p>
  </section>

  <div class="ribbon red blog-ribbon abs">Our Blog</div>

  <article class="post abs" style="top:1890px">
    <div class="post-meta"><span>On 02.19.10,</span><span>In <em>Blog Theme</em>,</span><span>by <em>admin</em></span></div>
    <div class="post-thumb" role="img" aria-label="Photo of a brick house with a green lawn"></div>
    <p class="post-text">Lorem ipsum dolor sit amet, consectetur adipiscing elit, sed do eiusmod tempor incididunt ut labore et dolore magna aliquaex ea commodo consequat.</p>
    <div class="post-actions"><span class="count">12 Comments</span><span class="reply">Leave your Comments</span></div>
  </article>
  <article class="post abs" style="top:2103px">
    <div class="post-meta"><span>On 02.19.10,</span><span>In <em>Blog Theme</em>,</span><span>by <em>admin</em></span></div>
    <div class="post-thumb" role="img" aria-label="Photo of a brick house with a green lawn"></div>
    <p class="post-text">Lorem ipsum dolor sit amet, consectetur adipiscing elit, sed do eiusmod tempor incididunt ut labore et dolore magna aliquaex ea commodo consequat.</p>
    <div class="post-actions"><span class="count">12 Comments</span><span class="reply">Leave your Comments</span></div>
  </article>
  <article class="post abs" style="top:2316px">
    <div class="post-meta"><span>On 02.19.10,</span><span>In <em>Blog Theme</em>,</span><span>by <em>admin</em></span></div>
    <div class="post-thumb" role="img" aria-label="Photo of a brick house with a green lawn"></div>
    <p class="post-text">Lorem ipsum dolor sit amet, consectetur adipiscing elit, sed do eiusmod tempor incididunt ut labore et dolore magna aliquaex ea commodo consequat.</p>
    <div class="post-actions"><span class="count">12 Comments</span><span class="reply">Leave your Comments</span></div>
  </article>

  <div class="pager abs"><span class="on">1</span><span>2</span><span>3</span></div>
  <div class="ribbon blue archive-ribbon abs">Archives</div>
  <div class="tags abs"><span>Sell My House</span><span>Fast Cash for Homes</span><span>We Buy Houses</span><span>Real Estate Investor</span><span>Latest</span></div>

  <aside>
    <div class="privacy-tab abs">Our Privacy Policy</div>
    <div class="side-social abs"><span></span><span></span><span></span><span></span><span></span></div>
    <div class="call-bar abs">CALL US 8AM TO 10 PM EASTERN TIME.<br>WE ANSWER OUR PHONES.</div>

    <div class="side-box abs" style="top:1378px;height:207px"><div class="inner">
      <h3 class="side-title">Home Seller Testimonials</h3>
      <p class="side-copy">I just wanted to thank you for buying my home in Winter Park. You made it fast and easy and kept me well informed the whole way.</p>
      <p class="quote-by"><b>Corwin Hale</b> – Winter Park</p>
    </div></div>

    <div class="side-box abs" style="top:1606px;height:183px"><div class="inner" style="position:relative">
      <h3 class="side-title">About Us</h3>
      <p class="side-copy" style="width:250px">Owned and operated in Orlando Florida since 2001. Oldest Continuous operated website in country.</p>
      <div class="about-photo" role="img" aria-label="Portrait photo of the company owner" style="top:0;right:0"></div>
    </div></div>

    <div class="side-box abs" style="top:1809px;height:605px"><div class="inner">
      <h3 class="side-title">Some of the Cities where<br>we buy houses. Not all are listed.</h3>
      <p class="side-copy">These are the cities where we have an affiliate where you can sell a home fast or quickly and we buy homes:</p>
      <div class="cities">
        <span>Orlando</span><span>Harrisburg</span>
        <span>Jacksonville</span><span>Virginia Beach</span>
        <span>Ft Myers</span><span>Virginia Homes</span>
        <span>Tampa</span><span>Greensboro</span>
        <span>St Pete</span><span>Charleston SC</span>
        <span>Gainesville</span><span>Flint Rochester</span>
        <span>Tallahassee</span><span>Lake Florida</span>
        <span>Melbourne</span><span>Wilmington</span>
        <span>West Palm Beach</span><span>Columbia</span>
        <span>Apopka</span><span>Titusville</span>
        <span>Deland</span><span>Valdosta</span>
        <span>Kissimmee</span><span>Houston</span>
        <span>Camden Atlanta</span><span>Detroit</span>
        <span>San Antonio</span><span>Phoenix</span>
      </div>
      <p class="view-all">View All Cities</p>
      <p class="note-red">If you don't see your city, we still probably buy homes there.</p>
    </div></div>

    <div class="side-box abs" style="top:2452px;height:242px"><div class="inner">
      <h3 class="side-title">We Buy</h3>
      <div class="buy-pics">
        <div role="img" aria-label="Photo of a large suburban house"></div>
        <div role="img" aria-label="Photo of a brick house with a front lawn"></div>
      </div>
      <p class="side-copy">We buy nice pretty houses and some ugly ones as well.</p>
    </div></div>
  </aside>

  <footer>
    <div class="site-footer abs"></div>
    <div class="foot-col abs" style="left:110px;width:230px">
      <h4 class="foot-title">WHY US</h4>
      <p class="foot-text">Lorem ipsum dolor sit amet, consectetur adipiscing elit. Aenean libero tortor, auctor et blandit in, facilisis sed nulla. Vivamus condimentum</p>
    </div>
    <div class="foot-col abs" style="left:433px;width:190px">
      <h4 class="foot-title">SITE LINKS</h4>
      <ul class="foot-list"><li>Sell Your Home</li><li>How it works</li><li>Stop foreclosure</li><li>Probate</li><li>Contact</li></ul>
    </div>
    <div class="foot-col abs" style="left:655px;width:190px">
      <h4 class="foot-title">GET SOCIAL</h4>
      <ul class="foot-list"><li><span class="dot"></span>Neighborly</li><li><span class="dot"></span>Chirper</li><li><span class="dot"></span>Circles</li><li><span class="dot"></span>ProLink</li></ul>
    </div>
    <div class="foot-col abs" style="left:872px;width:230px">
      <h4 class="foot-title">STAY IN TOUCH</h4>
      <div class="contact-line"><svg width="12" height="16" viewBox="0 0 12 16" aria-hidden="true"><path d="M6 0a6 6 0 0 0-6 6c0 4.5 6 10 6 10s6-5.5 6-10a6 6 0 0 0-6-6zm0 8.5A2.5 2.5 0 1 1 6 3.5a2.5 2.5 0 0 1 0 5z" fill="#888"/></svg><span>418 Alder Lane<br>Suite 12 Winter Park<br>FL 32789</span></div>
      <div class="contact-line"><svg width="14" height="14" viewBox="0 0 24 24" aria-hidden="true"><path fill="#888" d="M6.6 10.8a15 15 0 0 0 6.6 6.6l2.2-2.2c.3-.3.7-.4 1-.2 1.1.4 2.3.6 3.6.6.6 0 1 .4 1 1V20c0 .6-.4 1-1 1A17 17 0 0 1 3 4c0-.6.4-1 1-1h3.5c.6 0 1 .4 1 1 0 1.3.2 2.5.6 3.6.1.3 0 .7-.2 1z"/></svg><span>407-555-0142</span></div>
      <div class="contact-line"><svg width="14" height="12" viewBox="0 0 14 12" aria-hidden="true"><rect x=".5" y=".5" width="13" height="11" fill="none" stroke="#888"/><path d="M.5.5l6.5 6 6.5-6" fill="none" stroke="#888"/></svg><a>office@quickdeedsale.com</a></div>
    </div>
    <div class="legal abs"><span class="left">Copyright © 2015 . Quick Deed Sale All right Reserved</span><span class="right">Privacy Policy | Terms &amp; Conditions</span></div>
  </footer>

</div>
</body>
</html>
```